Founder / concept developer needs business card // Consultant needs VCARD

I need a business card for me as a founding consultant in Berlin. I advise entrepreneurs, especially in the design of business ideas, business plans or financing applications. More information about this in the annexes. My USP: I design / structure complex ideas and projects convincingly so that my client is successful. I want to communicate professionalism, effectiveness and clarity. Colors like from the range BLACK-GRAY-GREEN. I am 27 years old, I have studied business for 7 years. Attachments: - Business card design (only idea, do not focus on it) - Website screenshot (only idea, do not focus on it)

Target Market(s)

Target group: Founder (20-50 yrs, m / w, needy, in "break-up phase") and CONTRACTOR / "financier" (30-55 yrs, m / w, often public service "routine-oriented"). The foundations are in quite different industries: digital, craft, tourism, retail, services, etc. Almost all German.

Industry/Entity Type

Consultant

Contact Information for Business Card

Lukas Brennwald
M. Sc., International Business Administration
Gründungsberater, Konzeptentwickler
www.kelvoran-mitrel.de
Postfach-Zugang@kelvoran.de
Tel. 0481 294 3172

Colors

Designer to choose colors to be used in the design.

Requirements
Must have
• Professionalism, persuasiveness, clarity
Nice to have
• memorability
Should not have
• Schnörkelei

```html
<!DOCTYPE html>
<html lang="de">
<head>
<meta charset="utf-8">
<title>Visitenkarte – Lukas Brennwald</title>
<link rel="stylesheet" href="https://fonts.googleapis.com/css2?family=Open+Sans:wght@400;600&display=swap">
<style>
  :root {
    --page: #2b2724;
    --card: #0f0f0f;
    --card-edge: #1c1c1c;
    --green: #3fae3a;
    --green-soft: #8fd08a;
    --text: #f2f2f2;
    --muted: #d6d6d6;
  }
  * { box-sizing: border-box; margin: 0; padding: 0; }
  html, body {
    width: 1200px; height: 900px; overflow: hidden;
    background: var(--page);
    font-family: "Open Sans", Arial, sans-serif;
  }
  .stage {
    width: 1200px; height: 900px;
    display: flex; align-items: center; justify-content: center; gap: 48px;
  }
  .card {
    width: 530px; height: 316px;
    background: var(--card);
    border: 1px solid var(--card-edge);
    position: relative;
    box-shadow: 0 12px 30px rgba(0,0,0,.45);
  }
  /* front side */
  .card--front { display: flex; align-items: center; }
  .brand {
    width: 230px; height: 100%;
    display: flex; align-items: center; justify-content: center; gap: 10px;
  }
  .brand__square { width: 18px; height: 18px; background: var(--green); }
  .brand__name {
    color: var(--green); font-weight: 600; font-size: 22px; letter-spacing: .5px;
  }
  .divider {
    width: 1px; height: 150px;
    background: linear-gradient(to bottom, transparent, var(--green), transparent);
  }
  .contact { padding-left: 26px; color: var(--text); }
  .contact__name {
    color: var(--green); font-size: 20px; font-weight: 400; letter-spacing: .3px;
    text-transform: uppercase; line-height: 1.1;
  }
  .contact__role { font-size: 14px; color: var(--muted); margin-bottom: 20px; }
  .contact__list { list-style: none; }
  .contact__item {
    display: flex; align-items: center; gap: 10px;
    font-size: 14px; line-height: 21px;
  }
  .contact__icon { width: 11px; height: 11px; flex: none; fill: var(--green); }
  .contact__address { font-size: 14px; line-height: 21px; margin-top: 16px; }
  /* back side */
  .card--back { display: flex; align-items: center; justify-content: center; gap: 14px; }
  .card--back .brand__square { width: 26px; height: 26px; }
  .card--back .brand__name { font-size: 32px; }
</style>
</head>
<body>
<main class="stage">
  <section class="card card--front" aria-label="Vorderseite">
    <div class="brand">
      <span class="brand__square"></span>
      <span class="brand__name">KELVORAN</span>
    </div>
    <div class="divider"></div>
    <div class="contact">
      <h1 class="contact__name">Lukas Brennwald</h1>
      <p class="contact__role">Gründungsberater</p>
      <ul class="contact__list">
        <li class="contact__item">
          <svg class="contact__icon" viewBox="0 0 12 12" aria-hidden="true"><path d="M2.4 0.6 4.2 2.6 3.2 4.1c.7 1.6 2 2.9 3.7 3.7l1.5-1 2 1.8-.9 2.1C5 10.5 1.4 7 .4 1.6z"/></svg>
          0481 294 3172
        </li>
        <li class="contact__item">
          <svg class="contact__icon" viewBox="0 0 12 12" aria-hidden="true"><path d="M0 2h12v8H0z M1 3l5 3.5L11 3v-.2H1z" fill-rule="evenodd"/></svg>
          Postfach-Zugang@kelvoran.de
        </li>
        <li class="contact__item">
          <svg class="contact__icon" viewBox="0 0 12 12" aria-hidden="true"><circle cx="6" cy="6" r="6"/></svg>
          www.kelvoran-mitrel.de
        </li>
      </ul>
      <p class="contact__address">Lindenallee 14,<br>Berlin, 10115</p>
    </div>
  </section>

  <section class="card card--back" aria-label="Rückseite">
    <span class="brand__square"></span>
    <span class="brand__name">KELVORAN</span>
  </section>
</main>
</body>
</html>
```